Custom unique Stationary design for Logistics company

We need a custom, unique , elegant and luxurious full stationary design using our new logo, following these guidelines:
1- Business card: double sided, both sides uses the navy blue as the background main color (same as the code of the navy blue used in our logo).
2- envelope and folder: also use the same navy blue as the main background color.
3- book cover( notepad cover) : same thing with the navy blue
4- letterhead: feel free to use the combination of the colors in our logo.
5- rest of the items are up to your creativity

Target Market(s)

corporates and other businesses

Industry/Entity Type

Logistics and heavy machines contractors

Requirements
Must have
• Letterhead, business card, envelope, notepad cover, paper, file
Nice to have
• navy blue to be main background color for business card, envelope, notepad cover

```html
<!DOCTYPE html>
<html lang="en">
<head>
<meta charset="utf-8">
<title>Keelway Logistics – Business Card</title>
<link rel="stylesheet" href="https://fonts.googleapis.com/css2?family=Arimo:wght@400;700&display=swap">
<style>
  :root {
    --backdrop: #3a3a3a;
    --backdrop-edge: #1f1f1f;
    --navy: #02507a;
    --orange: #f0642b;
    --white: #ffffff;
    --rule: rgba(255,255,255,0.35);
  }
  html, body {
    margin: 0;
    width: 1200px;
    height: 900px;
    overflow: hidden;
  }
  body {
    background: radial-gradient(ellipse at center, var(--backdrop) 0%, var(--backdrop-edge) 100%);
    font-family: "Arimo", Arial, sans-serif;
    position: relative;
  }
  .card {
    position: absolute;
    top: 300px;
    width: 520px;
    height: 300px;
    border-radius: 24px;
    background: var(--navy);
    box-shadow: 0 14px 30px rgba(0,0,0,0.45);
    color: var(--white);
  }
  .card--front { left: 50px; }
  .card--back { left: 630px; }

  .brand {
    position: absolute;
    display: flex;
    align-items: center;
    gap: 10px;
  }
  .brand__dot {
    width: 16px;
    height: 16px;
    border-radius: 50%;
    background: var(--orange);
    flex: none;
  }
  .brand__name {
    font-weight: 700;
    color: var(--white);
    line-height: 1.05;
    letter-spacing: 0.5px;
  }
  .card--front .brand { left: 38px; top: 128px; }
  .card--front .brand__name { font-size: 27px; }
  .card--back .brand { left: 50%; top: 50%; transform: translate(-50%, -50%); }
  .card--back .brand__name { font-size: 38px; }
  .card--back .brand__dot { width: 22px; height: 22px; }

  .divider {
    position: absolute;
    left: 236px;
    top: 46px;
    width: 1px;
    height: 208px;
    background: var(--rule);
  }

  .contact {
    position: absolute;
    left: 262px;
    top: 54px;
    font-size: 14px;
    line-height: 1.3;
  }
  .contact__name {
    margin: 0;
    color: var(--orange);
    font-size: 17px;
    font-weight: 400;
    text-transform: uppercase;
    letter-spacing: 0.3px;
  }
  .contact__role {
    margin: 2px 0 14px;
    font-size: 15px;
  }
  .contact__list {
    list-style: none;
    margin: 0 0 12px;
    padding: 0;
  }
  .contact__item {
    display: flex;
    align-items: center;
    gap: 8px;
    margin-bottom: 3px;
  }
  .contact__icon {
    width: 13px;
    height: 13px;
    flex: none;
  }
  .contact__address {
    margin: 0;
    font-style: normal;
    padding-left: 21px;
  }
</style>
</head>
<body>

<section class="card card--front" aria-label="Business card, contact side">
  <div class="brand">
    <span class="brand__dot"></span>
    <span class="brand__name">Keelway<br>Logistics</span>
  </div>

  <div class="divider"></div>

  <div class="contact">
    <h1 class="contact__name">Daniel Moreau</h1>
    <p class="contact__role">Managing Director</p>
    <ul class="contact__list">
      <li class="contact__item">
        <svg class="contact__icon" viewBox="0 0 16 16" aria-hidden="true">
          <path d="M3.5 1.5l2.5 3-1.6 1.6a9 9 0 0 0 5.5 5.5L11.5 10l3 2.5-1.5 2a2 2 0 0 1-2 .5A13 13 0 0 1 1 5a2 2 0 0 1 .5-2z" fill="var(--orange)"/>
        </svg>
        055-210 734 618
      </li>
      <li class="contact__item">
        <svg class="contact__icon" viewBox="0 0 16 16" aria-hidden="true">
          <rect x="1" y="3" width="14" height="10" fill="var(--orange)"/>
          <path d="M1 3l7 6 7-6" fill="none" stroke="var(--navy)" stroke-width="1.3"/>
        </svg>
        hello@keelway.com
      </li>
      <li class="contact__item">
        <svg class="contact__icon" viewBox="0 0 16 16" aria-hidden="true">
          <g fill="none" stroke="var(--orange)" stroke-width="1.3">
            <circle cx="8" cy="8" r="6.5"/>
            <ellipse cx="8" cy="8" rx="3" ry="6.5"/>
            <path d="M1.5 8h13M2.5 4.8h11M2.5 11.2h11"/>
          </g>
        </svg>
        www.keelwaylogistics.com
      </li>
    </ul>
    <address class="contact__address">87, Harbour Road, Dock Gate 3<br>30218, Portmere</address>
  </div>
</section>

<section class="card card--back" aria-label="Business card, brand side">
  <div class="brand">
    <span class="brand__dot"></span>
    <span class="brand__name">Keelway<br>Logistics</span>
  </div>
</section>

</body>
</html>
```